Business Card Design For Office Furniture Clearance Company

Kestrel Office Clearance - our company name pretty much explains what we do, we clear offices for high end clients, mainly plc's and large international companies.

We require a nice looking business card that displays professionalism but without being too serious.

It would be nice to see just a little more than a conventional boring business card, make sure you add some flare.

Industry/Entity Type

Office Furniture

Contact Information for Business Card

CARD 1

Mark Holloway
Director
mark@kestrelofficeclearance.co.uk
m: 07700 153928

t: 01632 960418
www.kestrelofficeclearance.co.uk

Kestrel Office Clearance
Unit K4 B
2-8 Fenwick Lane
Harwell Park
Dunmore
ZZ9 4QT

free office clearances… you cant get better than that.

CARD 2

Peter Radford
Director
peter@kestrelofficeclearance.co.uk
m: 07700 382615

t: 01632 960418

Kestrel Office Clearance
Unit K4 B
2-8 Fenwick Lane
Harwell Park
Dunmore
ZZ9 4QT

Font styles to use
Sans Serif

Requirements
Must have
• A white background - as we have a blue logo.
Nice to have
• Nice use of the logo - play around with this and dissect it.

```html
<!DOCTYPE html>
<html lang="en">
<head>
<meta charset="utf-8">
<title>Kestrel Office Clearance – Business Card</title>
<link rel="stylesheet" href="https://fonts.googleapis.com/css2?family=Source+Sans+3:wght@400;600;700&display=swap">
<style>
  :root {
    --page-bg: #eceff2;
    --band-dark: #0a5d99;
    --band-light: #0a79c1;
    --brand-blue: #0b7bc3;
    --brand-text: #1170b5;
    --ring-fill: #e7ecf1;
    --ring-edge: #0d5e98;
    --card-white: #ffffff;
    --ink: #222a31;
    --on-blue: #ffffff;
  }
  html, body {
    margin: 0;
    width: 1200px;
    height: 900px;
    overflow: hidden;
    background: var(--page-bg);
    font-family: "Source Sans 3", sans-serif;
  }
  .canvas {
    position: relative;
    width: 1200px;
    height: 900px;
  }
  .business-card {
    position: absolute;
    left: 131px;
    top: 160px;
    width: 938px;
    height: 581px;
    filter: drop-shadow(0 10px 24px rgba(20, 40, 60, 0.18));
  }
  .card-base { fill: var(--card-white); }
  .band-top { fill: var(--band-dark); }
  .band-bottom { fill: var(--band-light); }
  .ring { fill: var(--ring-fill); }
  .ring-edge { fill: none; stroke: var(--ring-edge); stroke-width: 5; }
  .brand-disc { fill: var(--brand-blue); }
  .brand-word { fill: var(--on-blue); font-weight: 600; font-size: 40px; }
  .person-name { fill: var(--on-blue); font-weight: 600; font-size: 24px; }
  .person-role { fill: var(--on-blue); font-weight: 400; font-size: 17px; }
  .company-name { fill: var(--brand-text); font-weight: 600; font-size: 21px; }
  .address-line { fill: var(--ink); font-weight: 400; font-size: 18px; }
  .contact-line { fill: var(--on-blue); font-weight: 400; font-size: 17px; }
  .contact-icon { fill: var(--on-blue); }
  .contact-icon-line { fill: none; stroke: var(--on-blue); stroke-width: 1.4; }
</style>
</head>
<body>
<main class="canvas">
  <svg class="business-card" viewBox="0 0 670 415" xmlns="http://www.w3.org/2000/svg" aria-label="Kestrel Office Clearance business card">
    <rect class="card-base" x="0" y="0" width="460" height="415"/>
    <rect class="band-top" x="0" y="0" width="460" height="117"/>
    <rect class="band-bottom" x="0" y="295" width="460" height="120"/>

    <circle class="ring" cx="460" cy="207.5" r="207"/>
    <path class="ring-edge" d="M460 3 A204.5 204.5 0 0 1 460 412"/>

    <circle class="brand-disc" cx="460" cy="205" r="138"/>
    <text class="brand-word" x="460" y="219" text-anchor="middle">Kestrel</text>

    <text class="person-name" x="32" y="50">Mark Holloway</text>
    <text class="person-role" x="32" y="73">Director</text>

    <text class="company-name" x="32" y="180">Kestrel Office Clearance</text>
    <text class="address-line" x="32" y="206">Unit K4 B, 2-8 Fenwick Lane</text>
    <text class="address-line" x="32" y="230">Harwell Park, Dunmore</text>
    <text class="address-line" x="32" y="254">ZZ9 4QT</text>

    <g class="icon-mobile">
      <rect class="contact-icon-line" x="35" y="304" width="8" height="13" rx="1.5"/>
      <rect class="contact-icon" x="38" y="314" width="2" height="1.5"/>
    </g>
    <path class="contact-icon icon-phone" d="M35 333 q1.5 -1.5 3 0 l2 2.5 q0.8 1.2 -0.4 2.2 l-1 0.8 q1.5 3 4.2 4.4 l0.8 -1 q1 -1.2 2.2 -0.4 l2.4 2 q1.4 1.4 0 3 q-2 2 -4.5 1 q-6 -2.6 -9.5 -8.8 q-1.2 -3.2 0.8 -5.8z"/>
    <g class="icon-mail">
      <rect class="contact-icon" x="34" y="363" width="12" height="9" rx="1"/>
      <path d="M34.5 363.8 L40 368.5 L45.5 363.8" fill="none" stroke="var(--band-light)" stroke-width="1.2"/>
    </g>
    <g class="icon-web">
      <circle class="contact-icon-line" cx="40" cy="396" r="6"/>
      <ellipse class="contact-icon-line" cx="40" cy="396" rx="2.6" ry="6"/>
      <line class="contact-icon-line" x1="34" y1="396" x2="46" y2="396"/>
    </g>

    <text class="contact-line" x="55" y="317">07700 153928</text>
    <text class="contact-line" x="55" y="345">01632 960418</text>
    <text class="contact-line" x="55" y="373">mark@kestrelofficeclearance.co.uk</text>
    <text class="contact-line" x="55" y="401">www.kestrelofficeclearance.co.uk</text>
  </svg>
</main>
</body>
</html>
```